Verantor Cargo Flower trade show brochure

We are an international freight forwarding company from South America specialising in perishable handling both through air freight and sea freight. We need a brochure to hand out to customers in the flower fair trade shows in which we participate - China, Holland, Russia, USA. We need something clean yet striking and modern emphasising our brand and with great emphasis on our strengths in the perishable/flower forwarding realm. Our company is a merger of 4 of the largest forwarders in Ecuador into one company called Verantor Cargo Group. We would like emphasis on the new brand, however we do require that each individual logo of the 4 companies is portrayed in some way in the brochure. We are also registered with a global freight forwarding association known as PLN which also must be mentioned. We would like a defined concept for perishable handling, something along the lines of (but not limited to) - first class travel - dont your flowers deserve the same ? Attached a JPEG file with our new website proposed design so that you have an idea of our tastes. Also attached is some basic text which can be used to put together the brochure. We would like some emphasis also on some fast data facts such as - 1. We ship to over 80 countries worldwide 2. we forward over 5000 tons of flowers per month 3. we track and trace over 150 shipments per day etc etc. Please also include our website adress - www.verantorcargo, and something along the lines of - Follow us on (logo Bizlinko), (logo Chatterbook), logo (squawker) and our contact email address - info@verantorcargo.example

Target Market(s)

Flower importers worldwide

Industry/Entity Type

Freight Forwarding

Font styles to use
Sans Serif

Colors
9bcb3b
acd036
9d9d9d
757575

Requirements
Must have
• Photos of freight forwarding concepts, cut flowers

```html
<!DOCTYPE html>
<html lang="en">
<head>
<meta charset="utf-8">
<title>Verantor Cargo — International Freight Forwarding</title>
<link href="https://fonts.googleapis.com/css2?family=Raleway:wght@300;400;700;800&family=Lato:wght@300;400&family=Noto+Serif:wght@400&display=swap" rel="stylesheet">
<style>
  :root {
    --green: #9bcb3b;
    --green-box: #8cbf3a;
    --green-overlay: rgba(140, 194, 58, 0.88);
    --grey-dark: #4f4f4f;
    --grey-mid: #757575;
    --grey-light: #9d9d9d;
    --white: #ffffff;
  }
  * { margin: 0; padding: 0; box-sizing: border-box; }
  html, body { width: 1200px; height: 423px; overflow: hidden; background: var(--white); }
  .spread { position: relative; width: 1200px; height: 423px; font-family: "Lato", sans-serif; }

  /* Left page */
  .page-left { position: absolute; left: 0; top: 0; width: 600px; height: 423px; overflow: hidden; }
  .cargo-photo {
    position: absolute; inset: 0;
    background:
      radial-gradient(ellipse at 68% 35%, #c9a98a 0%, #8e6f5a 30%, transparent 60%),
      linear-gradient(180deg, #e9e7e3 0%, #cfcac3 35%, #a39c92 70%, #7f7a73 100%);
  }
  .innovation-box {
    position: absolute; left: 45px; top: 97px; width: 330px; height: 138px;
    background: var(--green-overlay); border-radius: 6px; padding: 14px 18px;
    color: var(--white);
  }
  .innovation-box h2 { font-family: "Raleway", sans-serif; font-weight: 800; font-size: 22px; letter-spacing: 0.5px; margin-bottom: 6px; }
  .innovation-box p { font-size: 10.5px; line-height: 1.42; font-weight: 400; text-align: justify; }
  .page-num-left {
    position: absolute; left: 6px; bottom: 10px; width: 20px; height: 20px; border-radius: 50%;
    background: rgba(255,255,255,0.55); color: var(--grey-mid); font-size: 10px;
    display: flex; align-items: center; justify-content: center;
  }

  /* Right page */
  .page-right { position: absolute; left: 600px; top: 0; width: 600px; height: 423px; }
  .site-url { position: absolute; right: 29px; top: 6px; font-family: "Noto Serif", serif; font-size: 11px; color: var(--grey-mid); letter-spacing: 0.5px; }
  .section-title { position: absolute; left: 52px; top: 60px; font-family: "Raleway", sans-serif; font-weight: 300; font-size: 15.5px; color: var(--grey-mid); letter-spacing: 0.6px; }
  .section-title .accent { color: var(--green); }
  .intro { position: absolute; left: 52px; top: 98px; width: 248px; font-size: 10px; line-height: 1.52; color: var(--grey-mid); text-align: justify; }
  .intro strong { color: var(--grey-dark); font-weight: 400; }

  .fact { position: absolute; left: 51px; width: 236px; background: var(--grey-dark); display: flex; align-items: center; padding: 0 8px; }
  .fact .mark { flex: 0 0 26px; height: 26px; background: var(--green); margin-right: 10px; border-radius: 2px; }
  .fact p { font-family: "Noto Serif", serif; font-size: 10px; line-height: 1.45; color: var(--white); }
  .fact-countries { top: 220px; height: 37px; }
  .fact-tons { top: 267px; height: 42px; }
  .fact-tracking { top: 322px; height: 42px; }

  .services { position: absolute; left: 316px; top: 106px; width: 225px; height: 256px; background: var(--green-box); padding: 10px 12px; color: var(--white); }
  .services h3 { display: flex; align-items: center; font-family: "Raleway", sans-serif; font-weight: 700; font-size: 12px; letter-spacing: 0.3px; margin-bottom: 8px; }
  .services h3 .mark { width: 16px; height: 16px; background: var(--white); opacity: 0.9; border-radius: 2px; margin-right: 10px; }
  .services ol { list-style: none; counter-reset: svc; }
  .services li { counter-increment: svc; position: relative; padding-left: 22px; font-size: 8.3px; line-height: 1.3; font-weight: 300; margin-bottom: 5.3px; }
  .services li::before { content: counter(svc, decimal-leading-zero); position: absolute; left: 0; top: 0; font-size: 7px; opacity: 0.55; }
  .services li.highlight { font-weight: 400; }

  .tagline { position: absolute; left: 0; right: 0; top: 382px; padding-left: 310px; text-align: left; font-size: 13px; color: var(--grey-mid); font-weight: 400; letter-spacing: 0.2px; }
  .tagline .accent { color: var(--green); }
  .page-num-right {
    position: absolute; right: 10px; bottom: 9px; width: 20px; height: 20px; border-radius: 50%;
    background: #ececec; color: var(--grey-mid); font-size: 10px;
    display: flex; align-items: center; justify-content: center;
  }
</style>
</head>
<body>
<main class="spread">
  <section class="page-left">
    <div class="cargo-photo" role="img" aria-label="Photo of a worker loading a netted pallet of flower boxes inside an aircraft cargo hold"></div>
    <div class="innovation-box">
      <h2>INNOVATION:</h2>
      <p>Verantor Cargo is dedicated to continual improvement and an innovative approach to freight forwarding. We are currently in the process of upgrading our tailor made and industry specific software in order to provide faster, more accurate and more detailed information to our customers.</p>
    </div>
    <div class="page-num-left">4</div>
  </section>

  <section class="page-right">
    <div class="site-url">www.verantorcargo.com</div>
    <h1 class="section-title">INTERNATIONAL FREIGHT <span class="accent">FORWARDING</span></h1>
    <p class="intro">As an ICAF agent for all major airlines, we can offer our customers reliable and varied options for their perishable forwarding requirements. Our expert staff work tirelessly to ensure that your temperature sensitive cargo arrives to its destination using optimal routings and maximum <strong>cost-efficiency</strong></p>

    <div class="fact fact-countries"><span class="mark"></span><p>We ship to over 80 countries worldwide</p></div>
    <div class="fact fact-tons"><span class="mark"></span><p>We forward over 5,000 tones of flowers per month</p></div>
    <div class="fact fact-tracking"><span class="mark"></span><p>We track and trace over 150 shipments per day</p></div>

    <aside class="services">
      <h3><span class="mark"></span>VALUE-ADDED SERVICES</h3>
      <ol>
        <li>Leveraged purchasing power with all major carriers</li>
        <li>Tracking and tracing follow-up on all shipments</li>
        <li>Customized labelling and handling</li>
        <li>Gross vs chargeable reports by supplier</li>
        <li>Temperature and humidity control monitoring</li>
        <li>Customized shipment reporting</li>
        <li>Temperature control reports per supplier</li>
        <li>State of the art CCTV security systems ensuring your products integrity whilst in our possession</li>
        <li class="highlight">ISO 9001 Quality certified processes</li>
        <li>PLN member since January 2015. 5000 PLN partners all over the world</li>
        <li>Ability to offer full ULDs</li>
      </ol>
    </aside>

    <p class="tagline">Our <span class="accent">success</span> depends on the <span class="accent">success</span> of our customers</p>
    <div class="page-num-right">5</div>
  </section>
</main>
</body>
</html>
```